Business card for denture clinic Veltrimora

We need a new business card with our new logo. We are a denture clinic in New Zealand with our target market being 45+ years old. We would need a space on the back to write our patients next appointment on. We would space for only one appointment rather than a list. We will attach a photo showing an example of this. But of course, we would like to see your twist on this. We want it to be bold and easy to read and a good mixture of professional but modern. We have attached our logo to be used on the card.

Target Market(s)

People aged 45+ needing dentures

Industry/Entity Type

Dental

Contact Information for Business Card

We want our logo on the front and the space to write an appointment on the back. I've attached an example our our old business card showing this. We need to have the technicians details on the front.

Font styles to use
Sans Serif

Colors
0255a3
919191
fbfbfb

Requirements
Must have
• The following details:
• Liam Dorsett BDT, PGDipCDentTech Calverin
• Dental Prosthetist
• Phone numbers: 0800 47 3125
• 09 572 1394
• Email: liam@veltrimora.co.nz
• www.veltrimora.co.nz
• Address: 14 Marlow Crest Road
• Halbrook West
• Auckland 0793
Nice to have
• We would like our business cards to have more than just two colours as we want them to be more vibrant. We have uploaded an example of a business card we liked that showed this.

```html
<!DOCTYPE html>
<html lang="en">
<head>
<meta charset="utf-8">
<title>Veltrimora business card</title>
<link rel="stylesheet" href="https://fonts.googleapis.com/css2?family=Maven+Pro:wght@400;500;700&display=swap">
<style>
  :root {
    --brand-blue: #0270b9;
    --deep-blue: #0255a3;
    --accent-orange: #e2663a;
    --paper: #fbfbfb;
    --grey: #919191;
    --text-grey: #6f6f6f;
    --backdrop: #ebe7e1;
  }
  * { margin: 0; padding: 0; box-sizing: border-box; }
  html, body { width: 1200px; height: 987px; overflow: hidden; }
  body {
    background: var(--backdrop);
    font-family: "Maven Pro", sans-serif;
    position: relative;
  }
  .card {
    position: absolute;
    left: 293px;
    width: 615px;
    height: 352px;
    border-radius: 20px;
    background: #fff;
    overflow: hidden;
    box-shadow: 0 3px 8px rgba(0,0,0,.18);
  }
  .card-front { top: 130px; }
  .card-back { top: 505px; }
  .card-shape { position: absolute; inset: 0; width: 615px; height: 352px; }

  /* front */
  .brand-block {
    position: absolute; left: 0; right: 0; top: 38px;
    display: flex; flex-direction: column; align-items: center;
  }
  .brand-square { width: 56px; height: 56px; background: var(--brand-blue); border-radius: 3px; }
  .brand-name {
    margin-top: 8px;
    font-size: 30px; font-weight: 500; letter-spacing: 1.5px;
    color: var(--brand-blue); line-height: 1;
  }
  .brand-tagline {
    margin-top: 4px;
    font-size: 12px; letter-spacing: 3.2px; color: var(--grey);
  }
  .practitioner {
    position: absolute; left: 0; right: 0; top: 208px;
    text-align: center; color: #fff;
  }
  .practitioner-name { font-size: 23px; font-weight: 700; letter-spacing: .3px; }
  .practitioner-credentials { font-size: 16px; font-weight: 700; }
  .role-rule {
    position: absolute; left: 26px; right: 27px; top: 238px;
    display: flex; align-items: center; gap: 8px;
    color: #fff; font-size: 16px;
  }
  .role-rule::before, .role-rule::after {
    content: ""; flex: 1; height: 1px; background: rgba(255,255,255,.85);
  }
  .contact-address, .contact-lines {
    position: absolute;
    color: #fff; font-size: 16px; line-height: 23px; font-style: normal;
  }
  .contact-address { left: 26px; top: 270px; }
  .contact-lines { right: 27px; top: 265px; text-align: right; }
  .contact-label { font-weight: 700; }

  /* back */
  .back-brand {
    position: absolute; left: 43px; top: 82px;
    display: flex; align-items: center; gap: 12px;
  }
  .back-brand-square { width: 30px; height: 30px; background: #fff; border-radius: 3px; }
  .back-brand-name { color: #fff; font-size: 24px; font-weight: 500; letter-spacing: 1px; }
  .appointment-title {
    position: absolute; right: 31px; top: 70px;
    color: #fff; font-size: 25px; font-weight: 700;
  }
  .appointment-slot { position: absolute; left: 37px; right: 33px; top: 258px; }
  .appointment-row {
    display: flex; align-items: baseline;
    color: var(--text-grey); font-size: 18px;
  }
  .field { display: flex; align-items: baseline; }
  .field-date { width: 268px; }
  .field-time { flex: 1; }
  .dots { flex: 1; border-bottom: 1.5px dotted var(--grey); margin: 0 2px; transform: translateY(-4px); }
  .field-date .dots { margin-right: 8px; }
</style>
</head>
<body>

<section class="card card-front">
  <svg class="card-shape" viewBox="0 0 615 352" aria-hidden="true">
    <path d="M0,189 H338 C348,189 352,186 356,181" fill="none" stroke="var(--accent-orange)" stroke-width="9"/>
    <path d="M0,196 H346 C366,196 368,169 396,169 H615 V352 H0 Z" fill="var(--brand-blue)"/>
  </svg>
  <div class="brand-block">
    <div class="brand-square"></div>
    <div class="brand-name">VELTRIMORA</div>
    <div class="brand-tagline">THE DENTURE EXPERTS</div>
  </div>
  <div class="practitioner">
    <span class="practitioner-name">LIAM DORSETT</span>
    <span class="practitioner-credentials">BDT, PGDipCDentTech Calverin</span>
  </div>
  <div class="role-rule">Dental Prosthetist</div>
  <address class="contact-address">
    14 Marlow Crest Road<br>
    Halbrook West, Auckland 0793<br>
    www.veltrimora.co.nz
  </address>
  <div class="contact-lines">
    <span class="contact-label">P</span> : 0800 47 3125<br>
    <span class="contact-label">C</span> : 09 572 1394<br>
    liam@veltrimora.co.nz
  </div>
</section>

<section class="card card-back">
  <svg class="card-shape" viewBox="0 0 615 352" aria-hidden="true">
    <path d="M0,0 H615 V165 H284 C262,165 266,195 244,195 H0 Z" fill="var(--brand-blue)"/>
    <path d="M615,170 H286 C272,170 270,178 266,184" fill="none" stroke="var(--accent-orange)" stroke-width="9"/>
  </svg>
  <div class="back-brand">
    <div class="back-brand-square"></div>
    <div class="back-brand-name">VELTRIMORA</div>
  </div>
  <div class="appointment-title">NEXT APPOINTMENT</div>
  <div class="appointment-slot">
    <div class="appointment-row">
      <div class="field field-date">Date:<span class="dots"></span></div>
      <div class="field field-time">Time:<span class="dots"></span>AM/PM</div>
    </div>
  </div>
</section>

</body>
</html>
```